Kestrel Facilities Business Card Design

We would now like to design business cards with the new Kestrel Facilities logo

Target Market(s)

Professional

Industry/Entity Type

Professional services

Contact Information for Business Card

Employee name, title, phone number, email address, corporate office address and logo.

Font styles to use
Sans Serif

Colors
0054AA
0677BA
7BADD7
CADEEF
E8F1F8

Requirements
Must have
• My logo
Should not have
• any other pictures or images besides my logo

```html
<!DOCTYPE html>
<html lang="en">
<head>
<meta charset="utf-8">
<title>Kestrel Facilities Business Card</title>
<link href="https://fonts.googleapis.com/css2?family=Montserrat:wght@400;500;600;700&family=Josefin+Sans:wght@400&display=swap" rel="stylesheet">
<style>
  :root {
    --backdrop: #cfd0d2;
    --card-white: #ffffff;
    --brand-blue: #3578be;
    --brand-deep: #2f6fbe;
    --brand-pale: #e8f1f8;
    --ink: #1e1e1e;
    --logo-light: #dde3ea;
  }
  * { box-sizing: border-box; margin: 0; padding: 0; }
  html, body {
    width: 1200px; height: 813px; overflow: hidden;
    background: var(--backdrop);
  }
  .stage {
    position: relative; width: 1200px; height: 813px;
    display: flex; align-items: center; justify-content: center; gap: 40px;
  }
  .card {
    position: relative; width: 520px; height: 300px;
    border-radius: 24px; overflow: hidden;
    box-shadow: 0 10px 30px rgba(0,0,0,0.25);
  }
  .card-front { background: var(--card-white); }
  .card-back { background: var(--brand-blue); display: flex; align-items: center; justify-content: center; }

  .front-wordmark {
    position: absolute; top: 38px; right: 40px;
    display: flex; align-items: center; gap: 10px;
    font-family: "Montserrat", sans-serif; font-weight: 600;
    font-size: 22px; color: var(--brand-blue); letter-spacing: 0.5px;
  }
  .mark-square { width: 22px; height: 22px; background: var(--brand-blue); }

  .faint-block {
    position: absolute; left: 40px; top: 110px; width: 250px; height: 170px;
    background: var(--brand-pale);
  }

  .address {
    position: absolute; right: 40px; top: 130px; text-align: right;
    font-family: "Josefin Sans", sans-serif; font-size: 15px; line-height: 1.45;
    color: var(--ink);
  }

  .name-tab {
    position: absolute; left: 0; top: 98px; width: 12px; height: 46px;
    background: var(--brand-blue);
  }
  .person {
    position: absolute; left: 36px; top: 96px;
    font-family: "Montserrat", sans-serif;
  }
  .person-name {
    font-size: 22px; font-weight: 700; color: var(--brand-deep); letter-spacing: 0.5px;
  }
  .person-title { font-size: 14px; font-weight: 500; color: var(--ink); margin-top: 2px; }

  .contacts {
    position: absolute; left: 36px; bottom: 30px; list-style: none;
    font-family: "Montserrat", sans-serif; font-size: 13px; font-weight: 500; color: var(--ink);
  }
  .contacts li { display: flex; align-items: center; gap: 8px; line-height: 22px; }
  .contacts svg { width: 14px; height: 14px; flex: none; }

  .back-wordmark {
    display: flex; align-items: center; gap: 14px;
    font-family: "Montserrat", sans-serif; font-weight: 600;
    font-size: 32px; color: var(--logo-light); letter-spacing: 0.5px;
  }
  .back-wordmark .mark-square { width: 32px; height: 32px; background: var(--logo-light); }
</style>
</head>
<body>
<main class="stage">
  <section class="card card-front" aria-label="Business card front">
    <div class="faint-block" aria-hidden="true"></div>
    <div class="front-wordmark"><span class="mark-square"></span>Kestrel Facilities</div>
    <address class="address">P.O Box 4410-00500<br>Thika, Kenya</address>
    <div class="name-tab"></div>
    <div class="person">
      <div class="person-name">AMARA KIVULI</div>
      <div class="person-title">Co-Founder</div>
    </div>
    <ul class="contacts">
      <li>
        <svg viewBox="0 0 16 16" aria-hidden="true"><path fill="var(--brand-blue)" d="M3 2h3l1.5 3.5-2 1.2a8 8 0 0 0 3.8 3.8l1.2-2L14 10v3a1 1 0 0 1-1 1A11 11 0 0 1 2 3a1 1 0 0 1 1-1z"/></svg>
        +254-700-41526
      </li>
      <li>
        <svg viewBox="0 0 16 16" aria-hidden="true"><rect x="1" y="3" width="14" height="10" rx="1" fill="var(--brand-blue)"/><path d="M1.5 3.5 8 9l6.5-5.5" fill="none" stroke="#fff" stroke-width="1.3"/></svg>
        hello@kestrelfac.co
      </li>
      <li>
        <svg viewBox="0 0 16 16" aria-hidden="true"><circle cx="8" cy="8" r="7" fill="var(--brand-blue)"/><path d="M1 8h14M8 1c3 3 3 11 0 14M8 1c-3 3-3 11 0 14" fill="none" stroke="#fff" stroke-width="1"/></svg>
        www.kestrelfac.co
      </li>
    </ul>
  </section>

  <section class="card card-back" aria-label="Business card back">
    <div class="back-wordmark"><span class="mark-square"></span>Kestrel Facilities</div>
  </section>
</main>
</body>
</html>
```